Coastline Premier Retreats Business Card Design

Design a business card for Coastline Premier Retreats. Look at the website for colors and reference. Card should have logo, name, title, office number, mobile number, email, URL and a tagline like, "Luxury Hotel & Resort Email Marketing" (This might change).

https://www.coastlinepremierretreats.example

The rest I will leave up to your imagination.

Contact Information for Business Card

Logo, name, title, office number, mobile number, email, URL and a tagline like, "Luxury Hotel & Resort Email Marketing" (This might change).

```html
<!DOCTYPE html>
<html lang="en">
<head>
<meta charset="utf-8">
<title>Coastline Premier Retreats – Business Card</title>
<link rel="stylesheet" href="https://fonts.googleapis.com/css2?family=Montserrat:wght@400;500;700;800&display=swap">
<style>
  :root {
    --stage: #2b2b2b;
    --card: #1a1a1a;
    --orange: #f07a1a;
    --white: #ffffff;
    --muted: #e9e9e9;
  }
  * { box-sizing: border-box; margin: 0; padding: 0; }
  html, body {
    width: 1200px; height: 900px; overflow: hidden;
    background: var(--stage);
    font-family: "Montserrat", sans-serif;
  }
  .canvas {
    position: relative; width: 1200px; height: 900px;
  }
  .card {
    position: absolute; left: 250px;
    width: 700px; height: 400px;
    background: var(--card);
    border-left: 3px solid var(--orange);
    border-bottom: 3px solid var(--orange);
    box-shadow: 0 18px 40px rgba(0,0,0,.45);
    overflow: hidden;
  }
  .card--front { top: 35px; }
  .card--back { top: 465px; }

  .wordmark {
    color: var(--white);
    font-weight: 800;
    text-transform: uppercase;
    letter-spacing: .04em;
    line-height: 1.1;
  }
  .card--front .wordmark {
    position: absolute; left: 0; right: 0; top: 130px;
    text-align: center; font-size: 40px;
  }
  .tagline {
    position: absolute; left: 0; right: 0; top: 300px;
    text-align: center;
    color: var(--orange);
    font-size: 17px; font-weight: 500; letter-spacing: .03em;
  }

  .card--back .wordmark {
    position: absolute; right: 40px; top: 60px;
    width: 270px; text-align: right; font-size: 22px;
  }
  .accent-block {
    position: absolute; left: 0; top: 70px;
    width: 16px; height: 40px; background: var(--orange);
  }
  .person { position: absolute; left: 60px; top: 58px; }
  .person__name {
    color: var(--orange); font-weight: 800; font-size: 34px;
    letter-spacing: .03em; text-transform: uppercase;
  }
  .person__title {
    color: var(--muted); font-size: 17px; font-weight: 400; margin-top: 2px;
  }
  .address {
    position: absolute; left: 110px; top: 195px;
    color: var(--muted); font-size: 16px; line-height: 1.35;
  }
  .contacts {
    position: absolute; left: 85px; top: 262px;
    list-style: none;
    color: var(--muted); font-size: 16px; line-height: 1.55;
  }
  .contacts li { display: flex; align-items: center; gap: 12px; }
  .contacts svg { width: 14px; height: 14px; fill: var(--orange); flex: none; }
</style>
</head>
<body>
<main class="canvas">

  <section class="card card--front">
    <h1 class="wordmark">Coastline Premier<br>Retreats</h1>
    <p class="tagline">Luxury Hotel &amp; Resort Email Marketing</p>
  </section>

  <section class="card card--back">
    <span class="accent-block"></span>
    <div class="person">
      <h2 class="person__name">Daniel Reyes</h2>
      <p class="person__title">CEO/Founder</p>
    </div>
    <p class="wordmark">Coastline Premier Retreats</p>

    <address class="address">
      Po Box, 48 B Harbor Rd<br>Seaview, CA 90412
    </address>

    <ul class="contacts">
      <li>
        <svg viewBox="0 0 16 16" aria-hidden="true"><path d="M4 0h8a1 1 0 0 1 1 1v14a1 1 0 0 1-1 1H4a1 1 0 0 1-1-1V1a1 1 0 0 1 1-1zm0 2v10h8V2zm4 11a1 1 0 1 0 0 2 1 1 0 0 0 0-2z"/></svg>
        555.014.2300
      </li>
      <li>
        <svg viewBox="0 0 16 16" aria-hidden="true"><path d="M3.6 1l2.3 2.8-1.3 1.6a9 9 0 0 0 6 6l1.6-1.3L15 12.4 13.2 15C6.5 14.6 1.4 9.5 1 2.8z"/></svg>
        +34 600 000 147
      </li>
      <li>
        <svg viewBox="0 0 16 16" aria-hidden="true"><path d="M1 3h14v10H1zm1.5 1.5v.3L8 8.6l5.5-3.8v-.3zm0 2.1v4.9h11V6.6L8 10.4z"/></svg>
        info@coastlinepremierretreats.example
      </li>
      <li>
        <svg viewBox="0 0 16 16" aria-hidden="true"><path d="M8 1a7 7 0 1 0 0 14A7 7 0 0 0 8 1zm0 1.5c.8 0 1.7 1.5 2 3.5H6c.3-2 1.2-3.5 2-3.5zM2.6 7h2.9a14 14 0 0 0 0 2H2.6a5.5 5.5 0 0 1 0-2zm3.9 0h3a13 13 0 0 1 0 2h-3a13 13 0 0 1 0-2zm4 0h2.9a5.5 5.5 0 0 1 0 2h-2.9a14 14 0 0 0 0-2zM6 10h4c-.3 2-1.2 3.5-2 3.5S6.3 12 6 10z"/></svg>
        www.coastlinepremierretreats.example
      </li>
    </ul>
  </section>

</main>
</body>
</html>
```